Pine Hollow Haven Home Inc. Website Update

We have a couple of broken links such as the "contact us" and would like to add board members and a calendar of events. We are open to a new design.

```html
<!DOCTYPE html>
<html lang="en">
<head>
<meta charset="utf-8">
<title>Pine Hollow Haven Home</title>
<link href="https://fonts.googleapis.com/css2?family=Open+Sans:wght@400;600;700&family=Poppins:wght@400;500;600&display=swap" rel="stylesheet">
<style>
:root{
  --blue:#1e7fc4;
  --blue-dark:#1565a8;
  --blue-band:#4f97cf;
  --pink:#e88fa8;
  --pink-deep:#e0708f;
  --yellow:#f1bd2d;
  --ink:#1c1c1c;
  --grey-bg:#f1efef;
  --footer:#262626;
  --white:#ffffff;
}
*{box-sizing:border-box;margin:0;padding:0}
html,body{width:1200px;height:3965px;overflow:hidden;background:var(--white)}
body{position:relative;font-family:"Poppins",sans-serif;color:var(--ink)}
.abs{position:absolute}
.brand{left:112px;top:22px;display:flex;align-items:center;gap:10px}
.brand-dot{width:52px;height:52px;border-radius:50%;background:var(--pink)}
.brand-name{font-size:17px;font-weight:600;color:var(--pink-deep);line-height:1.15;width:120px}
.contact-bar{top:36px;left:462px;display:flex;align-items:center;gap:44px;font-size:19px;font-weight:600}
.contact-bar .mail{font-size:15px;font-weight:400}
.contact-bar span{display:flex;align-items:center;gap:8px}
.socials{top:30px;left:976px;display:flex;gap:6px}
.socials i{width:26px;height:26px;border:2px solid var(--blue);border-radius:50%;display:block}
.nav{top:90px;left:298px;display:flex;gap:23px;font-size:14.5px}
.hero{top:140px;left:0;width:1200px;height:560px;background:linear-gradient(135deg,#5a4838,#8a6a52 40%,#c9a688 70%,#6b5544)}
.hero-title{top:410px;width:1200px;text-align:center;color:#fff;font-family:"Open Sans",sans-serif;font-weight:700;font-size:52px;line-height:1.2;letter-spacing:1px}
.btn{background:var(--blue);color:#fff;font-size:14px;display:inline-block;padding:13px 22px}
.hero-btn{top:555px;left:492px}
.chev{color:#fff;font-size:40px}
.seal{width:84px;height:84px;border-radius:50%;background:#fff;box-shadow:0 0 0 5px #fff;border:3px solid var(--pink);display:flex;align-items:center;justify-content:center;font-size:11px;font-weight:600;color:var(--pink-deep);text-align:center;line-height:1.1}
.about{top:730px;left:112px;width:976px;height:457px;background:var(--pink)}
.about-photo{top:790px;left:138px;width:332px;height:350px;background:linear-gradient(135deg,#8b7565,#d7c3b0 55%,#6e5b50)}
.about h2{position:absolute;left:400px;top:122px;color:#fff;font-family:"Open Sans",sans-serif;font-size:34px;font-weight:600}
.about p{position:absolute;left:400px;top:188px;width:510px;color:#fff;font-size:13.5px;line-height:1.95}
.about .btn{position:absolute;left:400px;top:367px;padding:12px 24px}
.h2{width:1200px;text-align:center;font-family:"Open Sans",sans-serif;font-weight:700;font-size:34px}
.h2 em{font-style:normal;color:var(--blue)}
.intro{top:1332px;width:1200px;text-align:center;font-size:19px;line-height:1.4}
.label{font-size:18px;text-align:center;line-height:1.3}
.board{top:1850px;left:0;width:1200px;height:555px;background:var(--grey-bg)}
.member{width:220px;text-align:center}
.member .pic{width:216px;height:216px;border-radius:50%;border:2px solid var(--pink);margin:0 auto;background:linear-gradient(160deg,#b7a89a,#6a5a50);box-shadow:inset 0 0 0 6px #fff}
.member b{display:block;margin-top:16px;font-size:20px;font-weight:600}
.member span{display:block;color:var(--blue);font-size:15px;margin-top:4px}
.services{top:2405px;left:0;width:1200px;height:445px;background:var(--blue-band);overflow:hidden}
.services h3{position:absolute;left:112px;top:82px;color:#fff;font-family:"Open Sans",sans-serif;font-size:32px;font-weight:700}
.list{position:absolute;list-style:none;color:#fff;font-size:20px}
.list li{height:41px;display:flex;align-items:center;gap:14px}
.more{position:absolute;left:698px;top:330px;color:#fff;font-size:19px}
.event{top:3028px;left:228px;width:745px;height:387px;border:2px solid var(--blue);background:#f2f2f2}
.event-photo{position:absolute;left:37px;top:42px;width:300px;height:303px;background:linear-gradient(135deg,#7a5c48,#c9a58a 50%,#4f3a30)}
.event h4{position:absolute;left:380px;top:42px;font-size:20px;font-weight:600}
.event .date{position:absolute;left:380px;top:80px;color:var(--blue-dark);font-family:"Open Sans",sans-serif;font-weight:700;font-size:20px}
.event p{position:absolute;left:380px;top:120px;width:330px;font-size:14.5px;line-height:1.9}
.event .btn{position:absolute;left:380px;top:282px;padding:10px 14px}
.arrow{font-size:44px;color:#333}
.footer{top:3560px;left:0;width:1200px;height:405px;background:var(--footer);color:#fff}
.footer h5{position:absolute;top:75px;font-size:20px;font-weight:600}
.fcol{position:absolute;top:120px;font-size:14.5px;line-height:1.5}
.fcol .row{display:flex;gap:18px;margin-bottom:22px}
.links{list-style:none;line-height:2.1}
.links li::before{content:"› ";}
.job{color:var(--pink)}
.copy{position:absolute;top:340px;width:1200px;text-align:center;font-size:13.5px}
</style>
</head>
<body>

<header>
  <div class="abs brand"><span class="brand-dot"></span><span class="brand-name">Pine Hollow Haven Home</span></div>
  <div class="abs contact-bar">
    <span><svg width="16" height="16" viewBox="0 0 24 24"><path fill="#1e7fc4" d="M6.6 10.8a15 15 0 0 0 6.6 6.6l2.2-2.2c.3-.3.7-.4 1-.2 1.1.4 2.3.6 3.6.6.6 0 1 .4 1 1V20c0 .6-.4 1-1 1C10.6 21 3 13.4 3 4c0-.6.4-1 1-1h3.5c.6 0 1 .4 1 1 0 1.3.2 2.5.6 3.6.1.3 0 .7-.2 1z"/></svg>555.014.2270</span>
    <span class="mail"><svg width="16" height="12" viewBox="0 0 16 12"><rect width="16" height="12" fill="#1e7fc4"/><path d="M0 0l8 6 8-6" stroke="#fff" fill="none"/></svg>hello@pinehollowhaven.org</span>
  </div>
  <div class="abs socials"><i></i><i></i><i></i></div>
  <nav class="abs nav"><span>Home</span><span>About</span><span>How You Can Help</span><span>Services Offered</span><span>Our Love of Pets</span><span>Contact Us</span><span>Haven Walk</span></nav>
</header>

<section>
  <div class="abs hero" role="img" aria-label="Photo of smiling young women working together at a table"></div>
  <div class="abs chev" style="left:44px;top:365px">&#8249;</div>
  <div class="abs chev" style="left:1108px;top:365px">&#8250;</div>
  <h1 class="abs hero-title">PINE HOLLOW<br>HAVEN HOME</h1>
  <span class="abs btn hero-btn">Learn About Our Mission</span>
  <svg class="abs" style="left:0;top:600px" width="1200" height="140" viewBox="0 0 1200 140">
    <path d="M0 40 Q600 140 1200 30 L1200 140 L0 140Z" fill="#fff"/>
    <path d="M0 40 Q600 140 1200 30 L1200 48 Q600 160 0 60Z" fill="#1e7fc4"/>
  </svg>
</section>

<section>
  <div class="abs about">
    <h2>About Us</h2>
    <p>Pine Hollow Haven Home is home to 11 girls ranging in ages from 12-21. The home has seven bedrooms and four bathrooms with a large spa tub for relaxing. Our kitchen takes on the aroma of a restaurant in the evenings as the girls practice their Independent Living Skills with menu planning and preparation in a supervised</p>
    <span class="btn">Read More</span>
  </div>
  <svg class="abs" style="left:112px;top:700px" width="976" height="60" viewBox="0 0 976 60"><path d="M0 0 H976 V30 Q488 -10 0 30Z" fill="#fff"/></svg>
  <div class="abs about-photo" role="img" aria-label="Photo of two young women studying with books"></div>
  <div class="abs seal" style="left:558px;top:690px">Pine Hollow</div>
</section>

<section>
  <h2 class="abs h2" style="top:1272px">We are <em>Pine Hollow Haven Home</em></h2>
  <p class="abs intro">With the help of our community, we have raised over 1000 girls and counting!<br>Some of the services we offer include:</p>
  <svg class="abs" style="left:0;top:1400px" width="1200" height="420" viewBox="0 0 1200 420">
    <g stroke="#f1bd2d" stroke-width="4">
      <line x1="383" y1="110" x2="600" y2="205"/><line x1="383" y1="307" x2="600" y2="205"/>
      <line x1="823" y1="110" x2="600" y2="205"/><line x1="823" y1="307" x2="600" y2="205"/>
    </g>
    <circle cx="600" cy="205" r="100" fill="#fff" stroke="#f1bd2d" stroke-width="22" stroke-dasharray="140 17"/>
    <circle cx="600" cy="205" r="78" fill="#fff"/>
    <g fill="#f1bd2d" stroke="#fff" stroke-width="3">
      <circle cx="383" cy="110" r="50"/><circle cx="383" cy="307" r="50"/>
      <circle cx="823" cy="110" r="50"/><circle cx="823" cy="307" r="50"/>
    </g>
    <g fill="none" stroke="#4a3a1a" stroke-width="2.5">
      <rect x="366" y="100" width="34" height="20"/><line x1="366" y1="108" x2="400" y2="108"/>
      <circle cx="383" cy="297" r="7"/><path d="M368 322 Q383 300 398 322"/>
      <circle cx="823" cy="100" r="9"/><path d="M806 128 Q823 106 840 128"/>
      <rect x="809" y="298" width="28" height="24"/><line x1="823" y1="298" x2="823" y2="322"/><line x1="806" y1="298" x2="840" y2="298"/>
    </g>
    <text x="600" y="200" text-anchor="middle" font-family="Poppins, sans-serif" font-size="15" font-weight="600" fill="#e0708f">Pine Hollow</text>
    <text x="600" y="220" text-anchor="middle" font-family="Poppins, sans-serif" font-size="15" font-weight="600" fill="#e0708f">Haven Home</text>
  </svg>
  <div class="abs label" style="left:115px;top:1473px;width:210px">Room, Board, and<br>Watchful Oversight</div>
  <div class="abs label" style="left:110px;top:1670px;width:220px">Transitional Living<br>Services</div>
  <div class="abs label" style="left:875px;top:1473px;width:220px">Independent Living<br>Services</div>
  <div class="abs label" style="left:880px;top:1697px;width:210px">Foster Gift Shop</div>
</section>

<section class="abs board">
  <h2 class="abs h2" style="top:83px">Board <em>Members</em></h2>
  <div class="abs member" style="left:162px;top:182px"><div class="pic" role="img" aria-label="Portrait of a board member"></div><b>Lorem ipsum</b><span>dolor sit amet</span></div>
  <div class="abs member" style="left:490px;top:182px"><div class="pic" role="img" aria-label="Portrait of a board member"></div><b>Lorem ipsum</b><span>dolor sit amet</span></div>
  <div class="abs member" style="left:818px;top:182px"><div class="pic" role="img" aria-label="Portrait of a board member"></div><b>Lorem ipsum</b><span>dolor sit amet</span></div>
</section>

<section class="abs services">
  <svg class="abs" style="left:0;top:0" width="1200" height="445"><polygon points="612,0 632,0 522,445 502,445" fill="#f1bd2d"/><polygon points="642,0 700,0 590,445 532,445" fill="#f1bd2d"/></svg>
  <h3>SERVICES OFFERED</h3>
  <ul class="list" style="left:112px;top:152px">
    <li><svg width="18" height="14"><path d="M2 7l5 5 9-10" stroke="#f1bd2d" stroke-width="3" fill="none"/></svg>Independent Living Housing</li>
    <li><svg width="18" height="14"><path d="M2 7l5 5 9-10" stroke="#f1bd2d" stroke-width="3" fill="none"/></svg>Life Skills Classes</li>
    <li><svg width="18" height="14"><path d="M2 7l5 5 9-10" stroke="#f1bd2d" stroke-width="3" fill="none"/></svg>Individual and Group Therapy</li>
    <li><svg width="18" height="14"><path d="M2 7l5 5 9-10" stroke="#f1bd2d" stroke-width="3" fill="none"/></svg>Behavior Modification</li>
    <li><svg width="18" height="14"><path d="M2 7l5 5 9-10" stroke="#f1bd2d" stroke-width="3" fill="none"/></svg>Positive Reinforcement</li>
  </ul>
  <ul class="list" style="left:698px;top:85px">
    <li><svg width="18" height="14"><path d="M2 7l5 5 9-10" stroke="#f1bd2d" stroke-width="3" fill="none"/></svg>Job Placement Assistance</li>
    <li><svg width="18" height="14"><path d="M2 7l5 5 9-10" stroke="#f1bd2d" stroke-width="3" fill="none"/></svg>Community Meetings</li>
    <li><svg width="18" height="14"><path d="M2 7l5 5 9-10" stroke="#f1bd2d" stroke-width="3" fill="none"/></svg>Menu Planning</li>
    <li><svg width="18" height="14"><path d="M2 7l5 5 9-10" stroke="#f1bd2d" stroke-width="3" fill="none"/></svg>Nutritional Counseling</li>
    <li><svg width="18" height="14"><path d="M2 7l5 5 9-10" stroke="#f1bd2d" stroke-width="3" fill="none"/></svg>SAT Preparation</li>
  </ul>
  <span class="more">Read More &gt;&gt;</span>
</section>

<section>
  <h2 class="abs h2" style="top:2935px">Calendar Of <em>Events</em></h2>
  <div class="abs arrow" style="left:160px;top:3190px">&#8249;</div>
  <div class="abs arrow" style="left:1010px;top:3190px">&#8250;</div>
  <div class="abs event">
    <div class="event-photo" role="img" aria-label="Photo of three smiling young women"></div>
    <h4>Sed ut perspiciatis unde</h4>
    <div class="date">Oct 18 2018</div>
    <p>omnis iste natus error sit voluptatem accusantium doloremque laudantium, totam rem aperiam, eaque ipsa quae ab illo inventore veritatis et quasi architecto beatae vitae dicta sunt</p>
    <span class="btn">Read More</span>
  </div>
</section>

<footer>
  <svg class="abs" style="left:0;top:3470px" width="1200" height="100" viewBox="0 0 1200 100">
    <path d="M0 90 Q600 -20 1200 90 L1200 100 L0 100Z" fill="#262626"/>
    <path d="M0 80 Q600 -30 1200 80 L1200 92 Q600 -18 0 92Z" fill="#1e7fc4"/>
  </svg>
  <div class="abs seal" style="left:558px;top:3478px">Pine Hollow</div>
  <div class="abs footer">
    <h5 style="left:112px">Contact Info</h5>
    <div class="fcol" style="left:112px">
      <div class="row"><svg width="12" height="18" viewBox="0 0 12 18"><path d="M6 0a6 6 0 0 0-6 6c0 5 6 12 6 12s6-7 6-12a6 6 0 0 0-6-6z" fill="#fff"/><circle cx="6" cy="6" r="2" fill="#262626"/></svg><span>418 Cedar Mill Rd, Ridgefield,<br>GA 30199, USA</span></div>
      <div class="row"><svg width="14" height="14" viewBox="0 0 24 24"><path fill="#fff" d="M6.6 10.8a15 15 0 0 0 6.6 6.6l2.2-2.2c.3-.3.7-.4 1-.2 1.1.4 2.3.6 3.6.6.6 0 1 .4 1 1V20c0 .6-.4 1-1 1C10.6 21 3 13.4 3 4c0-.6.4-1 1-1h3.5c.6 0 1 .4 1 1 0 1.3.2 2.5.6 3.6.1.3 0 .7-.2 1z"/></svg><span>555.014.2270</span></div>
      <div class="row"><svg width="16" height="12"><rect width="16" height="12" fill="#fff"/><path d="M0 0l8 6 8-6" stroke="#262626" fill="none"/></svg><span>hello@pinehollowhaven.org</span></div>
    </div>
    <h5 style="left:490px">Links</h5>
    <ul class="fcol links" style="left:490px;top:112px"><li>Home</li><li>About</li><li>How You Can Help</li><li>Services Offered</li><li>Our Love of Pets</li><li>Contact Us</li></ul>
    <h5 style="left:740px">Join Our Team</h5>
    <div class="fcol" style="left:740px;line-height:2.8">
      <div class="job">Overnight Shift House Parent</div>
      <div>Ridgefield, GA &nbsp;|&nbsp; Temporary &nbsp;|&nbsp; Salary: $11.00/hour</div>
      <div class="job">Direct Care Worker (DCW)</div>
      <div>Ridgefield, GA &nbsp;|&nbsp; Full-time</div>
    </div>
    <div class="copy">© PINE HOLLOW HAVEN HOME INC. 2018. ALL RIGHTS RESERVED</div>
  </div>
</footer>

</body>
</html>
```